Trade Show - double sided 4m wide graphic wall

I am attending a trade show where I am speaking on behalf of my former company. As part of the deal a 'stand space' is provided and all we are asked for is to provide the graphics in file format for the show organisers to produce.The stand had display boards of 4 x 1m wide and about 2.6m high. The wall has a small wraparound end graphic and then more panels on the revers so images are needed for both sides. A detail of the panel set-up is attached to this brief.The session I will be talking at is too small/medium e-commerce sellers who use Tradelo and Vendora as their main storefronts as well as their own websites. the company I'm representing are a fulfilment house. They hold their client's products in their warehouse and then receive orders from the clients end customers. My company then processes the orders, picks and packs the product and sends it out to the end consumer....in effect handles the whole warehousing and back end aspect. I wish this graphic to display our company branding and then have a theme or approach that holds this together with images that show the capabilities of the facilities we have available, as well as our capability to integrate with Vendora, Tradelo and other online stores. there will also be a few bullet points to integrate. I have attached details of the display panels I need. The specification is that they need to be 300dpi CMYK PDF's with 3mm bleed and offset crop marks (High res PDF file). I can supply you with a short video that shows you very quickly the type of thing we undertake that I hope may give you a feel for the business and I have a number of images and logos I can supply but would need to provide them via a dropbox link as there are too many and the sizes are too great to add to this request.I am coming to this requirement very late, so need to get a solution in place ASAP.

Target Market(s)

Trade Show Audience - Potential customers

Font styles to use
Sans Serif

Colors
85acd3
3377b5
33a6d7
32a6d6
ffffff

Requirements
Must have
• my company branding and images although others you may have access to and are related are fine.
Nice to have
• thoughts thus far are a collage or abstract backgroud image with more focused images in front but your the expert!

```html
<!DOCTYPE html>
<html lang="en">
<head>
<meta charset="utf-8">
<title>Kestrel Fulfilment – Trade Show Wall</title>
<link rel="stylesheet" href="https://fonts.googleapis.com/css2?family=Ubuntu:wght@400;500;700&display=swap">
<style>
  :root {
    --navy: #2b4470;
    --navy-deep: #253b63;
    --blue: #3377b5;
    --sky: #33a6d7;
    --pale: #85acd3;
    --white: #ffffff;
    --mist: #e4e8ee;
    --ink: #1f3566;
  }
  * { box-sizing: border-box; margin: 0; padding: 0; }
  html, body { width: 1200px; height: 609px; overflow: hidden; background: var(--white); }
  body { font-family: "Ubuntu", sans-serif; }

  .wall { position: relative; width: 1200px; height: 609px; }
  .wall-frame { position: absolute; left: 13px; top: 13px; width: 1174px; height: 584px; background: var(--navy-deep); }
  .wrap-end { position: absolute; top: 13px; width: 98px; height: 584px; display: flex; align-items: center; justify-content: center; }
  .wrap-end--left { left: 13px; }
  .wrap-end--right { right: 13px; }
  .wrap-end__url { color: var(--white); font-weight: 500; font-size: 25px; writing-mode: vertical-rl; transform: rotate(180deg); letter-spacing: .3px; }

  .main-panel { position: absolute; left: 111px; top: 13px; width: 978px; height: 584px; background: var(--navy); overflow: hidden; }
  .header-band { position: absolute; left: 0; top: 21px; width: 978px; height: 110px; }

  .brand { position: absolute; left: 378px; top: 29px; display: flex; align-items: center; gap: 10px; }
  .brand__mark { width: 54px; height: 54px; border-radius: 50%; background: var(--ink); flex: none; }
  .brand__name { color: var(--ink); font-weight: 500; font-size: 30px; line-height: 29px; letter-spacing: -.3px; }

  .hero-photo { position: absolute; width: 146px; height: 146px; border-radius: 50%; border: 4px solid var(--blue); }
  .hero-photo--left { left: 137px; top: 41px; background: radial-gradient(circle at 50% 70%, #e9d39a, #a0692c 45%, #3b2a22 90%); }
  .hero-photo--right { left: 695px; top: 41px; background: radial-gradient(circle at 50% 55%, #f0dfb8, #c69a58 50%, #4f6c9c 95%); }

  .headline { position: absolute; left: 250px; top: 129px; width: 480px; text-align: center; color: var(--white); font-weight: 400; font-size: 18px; line-height: 27.6px; text-transform: uppercase; }

  .capability-row { position: absolute; left: 17px; top: 226px; display: flex; gap: 6px; }
  .capability-row__photo { width: 151px; height: 113px; }
  .photo--footwear { background: linear-gradient(180deg, #f2efe9 0%, #d97b73 45%, #f0e6e0 55%, #c46458 100%); }
  .photo--retail { background: linear-gradient(135deg, #e2e6ee, #6f7fa0 50%, #d05d2e); }
  .photo--racking { background: linear-gradient(180deg, #4862a6, #c7b08a 50%, #e77a2c 80%, #7b6a58); }
  .photo--operations { background: linear-gradient(135deg, #dcdfe6, #8fa0b8 45%, #c8a24a 75%, #3f4f6d); }
  .photo--storage { background: linear-gradient(180deg, #8a4f1c, #e1a44c 50%, #f0cd86 80%, #b47a36); }
  .photo--dispatch { background: linear-gradient(180deg, #7fa6d8 0%, #c9d6e6 40%, #b0503c 60%, #6d6f78 100%); }

  .services { position: absolute; left: 92px; top: 349px; width: 794px; height: 78px; border: 2.5px solid var(--blue); border-radius: 18px; }
  .service { position: absolute; display: flex; align-items: center; gap: 7px; color: var(--white); font-weight: 500; font-size: 10.2px; text-transform: uppercase; white-space: nowrap; }
  .service--top { top: 4px; }
  .service--bottom { top: 35px; }
  .service__icon { width: 27px; height: 27px; border-radius: 50%; background: var(--mist); display: flex; align-items: center; justify-content: center; }
  .service__icon span { width: 11px; height: 11px; border: 1.3px solid #6b7a93; border-radius: 2px; }

  .web-pill { position: absolute; left: 348px; top: 435px; width: 282px; height: 30px; border-radius: 15px; background: var(--blue); display: flex; align-items: center; justify-content: center; gap: 6px; color: var(--white); font-weight: 500; font-size: 21px; }

  .contact-band { position: absolute; left: 0; top: 479px; width: 978px; height: 34px; }
  .contact__item { position: absolute; top: 490px; display: flex; align-items: center; gap: 6px; color: var(--ink); font-weight: 700; font-size: 11.5px; white-space: nowrap; }

  .marketplaces { position: absolute; left: 0; top: 526px; width: 978px; height: 32px; background: var(--white); display: flex; align-items: center; justify-content: space-between; padding: 0 14px; }
  .marketplaces__name { color: var(--ink); font-weight: 500; font-size: 15px; }
</style>
</head>
<body>
<div class="wall">
  <div class="wall-frame"></div>

  <aside class="wrap-end wrap-end--left"><span class="wrap-end__url">www.kestrelhub.com</span></aside>
  <aside class="wrap-end wrap-end--right"><span class="wrap-end__url">www.kestrelhub.com</span></aside>

  <section class="main-panel">
    <svg class="header-band" viewBox="0 0 978 110" aria-hidden="true">
      <defs>
        <linearGradient id="mistFade" x1="0" y1="0" x2="0" y2="1">
          <stop offset="0" stop-color="#f3f5f8"/>
          <stop offset="1" stop-color="#d9dee6"/>
        </linearGradient>
      </defs>
      <path d="M0 0 H978 V62 C830 62 800 62 760 80 C700 110 640 94 560 94 H0 Z" fill="url(#mistFade)"/>
    </svg>

    <div class="brand">
      <span class="brand__mark"></span>
      <span class="brand__name">kestrel<br>fulfilment</span>
    </div>

    <div class="hero-photo hero-photo--left" role="img" aria-label="Warehouse aisle with tall lit racking"></div>
    <div class="hero-photo hero-photo--right" role="img" aria-label="Warehouse racking with a worker in hi-vis"></div>

    <h1 class="headline">When it comes to logistics solutions,<br>we understand each business has<br>different needs</h1>

    <div class="capability-row">
      <div class="capability-row__photo photo--footwear" role="img" aria-label="Shelves of women's shoes"></div>
      <div class="capability-row__photo photo--retail" role="img" aria-label="Boxed retail stock and pick totes"></div>
      <div class="capability-row__photo photo--racking" role="img" aria-label="Racking filled with cartons"></div>
      <div class="capability-row__photo photo--operations" role="img" aria-label="Collage of warehouse operations"></div>
      <div class="capability-row__photo photo--storage" role="img" aria-label="Warm-lit storage aisle"></div>
      <div class="capability-row__photo photo--dispatch" role="img" aria-label="Lorry at the loading bay"></div>
    </div>

    <div class="services">
      <div class="service service--top" style="left:18px"><span class="service__icon"><span></span></span>Cosmetics logistics services</div>
      <div class="service service--top" style="left:221px"><span class="service__icon"><span></span></span>Fashion retail logistics</div>
      <div class="service service--top" style="left:400px"><span class="service__icon"><span></span></span>Marketing materials distribution</div>
      <div class="service service--top" style="left:644px"><span class="service__icon"><span></span></span>Travel logistics</div>
      <div class="service service--bottom" style="left:23px"><span class="service__icon"><span></span></span>Financial services logistics</div>
      <div class="service service--bottom" style="left:226px"><span class="service__icon"><span></span></span>Retail logistics</div>
      <div class="service service--bottom" style="left:361px"><span class="service__icon"><span></span></span>Information technology</div>
      <div class="service service--bottom" style="left:557px"><span class="service__icon"><span></span></span>Online food logistics services</div>
    </div>

    <div class="web-pill">
      <svg width="16" height="16" viewBox="0 0 16 16" aria-hidden="true"><circle cx="8" cy="8" r="6.5" fill="none" stroke="#fff" stroke-width="1.4"/><path d="M1.5 8H14.5M8 1.5C5 5 5 11 8 14.5M8 1.5C11 5 11 11 8 14.5" fill="none" stroke="#fff" stroke-width="1.1"/></svg>
      www.kestrelhub.com
    </div>

    <svg class="contact-band" viewBox="0 0 978 34" aria-hidden="true">
      <defs>
        <linearGradient id="bandFade" x1="0" y1="0" x2="1" y2="0">
          <stop offset="0" stop-color="#c9d1dc"/>
          <stop offset="1" stop-color="#f2f4f7"/>
        </linearGradient>
      </defs>
      <path d="M0 29 H300 C360 29 380 4 470 2 H978 V34 H0 Z" fill="#e9edf2"/>
      <path d="M0 33 H370 C400 33 410 8 480 6 H978 V34 H0 Z" fill="url(#bandFade)"/>
      <path d="M0 30 H360 C400 30 405 5 470 3 H978" fill="none" stroke="#fff" stroke-width="2"/>
    </svg>
    <span class="contact__item" style="left:471px">
      <svg width="10" height="10" viewBox="0 0 10 10" aria-hidden="true"><circle cx="5" cy="5" r="4.3" fill="none" stroke="#1f3566" stroke-width="1"/><path d="M3.5 3 Q3 5 5.5 7" fill="none" stroke="#1f3566" stroke-width="1.2"/></svg>
      +44 (0) 200 555 0142
    </span>
    <span class="contact__item" style="left:622px">+44 (0) 1700 555018</span>
    <span class="contact__item" style="left:758px">
      <svg width="14" height="10" viewBox="0 0 14 10" aria-hidden="true"><rect x=".6" y=".6" width="12.8" height="8.8" fill="none" stroke="#1f3566" stroke-width="1.1"/><path d="M.6 .6 7 6 13.4 .6" fill="none" stroke="#1f3566" stroke-width="1.1"/></svg>
      hello@kestrelhub.com
    </span>

    <div class="marketplaces">
      <span class="marketplaces__name">Vendora</span>
      <span class="marketplaces__name">Bazaro</span>
      <span class="marketplaces__name">Kaimono</span>
      <span class="marketplaces__name">Cartiva</span>
      <span class="marketplaces__name">Storely</span>
      <span class="marketplaces__name">Linkflow</span>
      <span class="marketplaces__name">Shopwell</span>
      <span class="marketplaces__name">BuyPress</span>
      <span class="marketplaces__name">Blocksite</span>
      <span class="marketplaces__name">Craftly</span>
      <span class="marketplaces__name">Tradelo</span>
    </div>
  </section>
</div>
</body>
</html>
```